Elegant Business Card for Technology Company

Client is a supplier of innovative industrial communications and automation equipment since 2002. This contest is to gather fresh ideas for a redesign of the existing business card. Client is looking for design that best communicates tagline "Industrial Networking and Computing Specialist".

Design submissions should look modern, clean, elegant and professional. It should not be cluttered. Use white as the primary colour. Orange and black as secondary colour. Refer to jpeg File 1 on the current design.

Fonts used by Client used include Arial Regular, Arial Black, Roboto Regular, Roboto Black and Lato.

The winning design will be sent for offset printing using super white 250gsm artcard paper (open for suggestions).

Target Market(s)

System Engineers, Project Managers, Purchasing Managers from companies providing engineering services for Smart Cities.

Industry/Entity Type

Information Technology

Contact Information for Business Card

Refer to PDF File 3 for Business Card Details. Priority of short contact information would be as follows Name > Job Title > Email > Mobile > Web > Tel > Fax > Business Address >UEN (UEN represents company registration number)

Font styles to use
Sans Serif

Colors
ffffff
f37122
000000
5c5c5c

Requirements
Must have
• Refer to AI File 2 (Company Logo) & PDF File 3 (Information on Namecard)
Should not have
• No QR codes
• No Social Media Icons
• Do not create full Black or Orange colour background

```html
<!DOCTYPE html>
<html lang="en">
<head>
<meta charset="utf-8">
<title>KVR Asia Pacific – Business Card</title>
<link href="https://fonts.googleapis.com/css2?family=Lato:wght@400;700&display=swap" rel="stylesheet">
<style>
  :root {
    --paper: #ffffff;
    --stage: #ecebe8;
    --ink: #000000;
    --grey: #5c5c5c;
    --orange: #f37122;
    --orange-light: #f6a936;
    --orange-deep: #e8701e;
  }
  * { box-sizing: border-box; margin: 0; padding: 0; }
  html, body { width: 1200px; height: 780px; overflow: hidden; }
  body {
    background: var(--stage);
    font-family: "Lato", Arial, sans-serif;
    color: var(--ink);
    position: relative;
  }
  .card {
    position: absolute;
    width: 540px;
    height: 324px;
    background: linear-gradient(135deg, #ffffff 0%, #f1f1f1 100%);
    box-shadow: 0 2px 0 #d8d8d8, 0 4px 0 #c9c9c9, 0 10px 24px rgba(0,0,0,.18);
    overflow: hidden;
  }
  .card--front { left: 40px; top: 228px; }
  .card--back  { left: 620px; top: 228px; }

  .rule { position: absolute; left: 0; width: 100%; height: 2px; background: var(--ink); }
  .band {
    position: absolute; left: 0; width: 100%;
    background: linear-gradient(100deg, var(--orange-deep) 0%, var(--orange-light) 55%, var(--orange) 100%);
    color: var(--paper);
  }

  /* brand lockup */
  .brand { position: absolute; display: flex; align-items: center; gap: 12px; }
  .brand__dot { width: 46px; height: 46px; border-radius: 50%; background: var(--orange); }
  .brand__name { font-weight: 700; font-size: 38px; line-height: 1; color: var(--ink); letter-spacing: 1px; }
  .brand__company { font-size: 14px; color: var(--ink); margin-top: 4px; }

  /* front */
  .card--front .band { top: 172px; height: 128px; }
  .card--front .rule--top { top: 168px; }
  .card--front .rule--bottom { top: 304px; }
  .card--front .brand { left: 30px; top: 84px; }
  .person { position: absolute; right: 30px; top: 28px; text-align: right; }
  .person__name { font-weight: 700; font-size: 24px; letter-spacing: .2px; }
  .person__title { font-size: 13px; color: var(--orange); margin-top: 2px; }

  .contacts { position: absolute; left: 30px; top: 20px; list-style: none; }
  .contacts li { display: flex; align-items: center; gap: 8px; font-size: 13.5px; line-height: 22px; }
  .contacts svg { width: 14px; height: 14px; flex: none; }

  .address { position: absolute; right: 30px; top: 24px; text-align: right; font-size: 14px; line-height: 22px; }

  /* back */
  .card--back .brand { left: 30px; top: 28px; }
  .card--back .rule--top { top: 108px; }
  .card--back .band { top: 112px; height: 186px; }
  .card--back .rule--bottom { top: 302px; }
  .tagline { position: absolute; left: 30px; top: 14px; font-size: 17px; letter-spacing: .3px; }
  .services { position: absolute; left: 30px; top: 48px; list-style: none; }
  .services li { font-size: 13.5px; line-height: 21px; color: #2a1a0e; position: relative; padding-left: 16px; }
  .services li::before {
    content: ""; position: absolute; left: 0; top: 7px;
    width: 7px; height: 7px; border-radius: 50%; background: var(--paper);
  }
  .web { position: absolute; right: 30px; bottom: 14px; font-size: 13px; font-weight: 700; }
</style>
</head>
<body>

<section class="card card--front" aria-label="Business card front">
  <div class="brand">
    <span class="brand__dot"></span>
    <div>
      <div class="brand__name">KVR</div>
      <div class="brand__company">KVR Asia Pacific Pte Ltd</div>
    </div>
  </div>

  <div class="person">
    <div class="person__name">Daniel Wong</div>
    <div class="person__title">Sales Manager</div>
  </div>

  <div class="rule rule--top"></div>
  <div class="band">
    <ul class="contacts">
      <li>
        <svg viewBox="0 0 14 14"><rect width="14" height="14" rx="2" fill="#fff"/><rect x="4.5" y="2.5" width="5" height="9" rx="1" fill="none" stroke="#f37122" stroke-width="1.3"/></svg>
        +65 9123 4567
      </li>
      <li>
        <svg viewBox="0 0 14 14"><rect width="14" height="14" rx="2" fill="#fff"/><path d="M4 3.5c0 4 2.5 6.5 6.5 6.5l.5-2-2-1-1 1c-1 -.5-2-1.5-2.5-2.5l1-1-1-2z" fill="#f37122"/></svg>
        +65 6234 5180
      </li>
      <li>
        <svg viewBox="0 0 14 14"><rect width="14" height="14" rx="2" fill="#fff"/><rect x="3" y="5" width="8" height="5" fill="none" stroke="#f37122" stroke-width="1.2"/><rect x="4.5" y="2.5" width="5" height="3" fill="#f37122"/></svg>
        +65 6234 5199
      </li>
      <li>
        <svg viewBox="0 0 14 14"><rect width="14" height="14" rx="2" fill="#fff"/><rect x="2.5" y="4" width="9" height="6" fill="none" stroke="#f37122" stroke-width="1.2"/><path d="M2.5 4l4.5 3.5 4.5-3.5" fill="none" stroke="#f37122" stroke-width="1.2"/></svg>
        sales@kvr.com.sg
      </li>
    </ul>
    <div class="address">
      UEN No &nbsp;200507314<br>
      22 Kallang Way Tech Hub<br>
      #05-12 (Block B), Singapore 349215
    </div>
  </div>
  <div class="rule rule--bottom"></div>
</section>

<section class="card card--back" aria-label="Business card back">
  <div class="brand">
    <span class="brand__dot"></span>
    <div>
      <div class="brand__name">KVR</div>
      <div class="brand__company">KVR Asia Pacific Pte Ltd</div>
    </div>
  </div>

  <div class="rule rule--top"></div>
  <div class="band">
    <p class="tagline">Industrial Networking and Computing Specialist</p>
    <ul class="services">
      <li>Industrial Ethernet / Wireless / Cellular</li>
      <li>Industrial and Embedded Computing</li>
      <li>Serial / Fieldbus Connectivity</li>
      <li>IP Video Surveillance</li>
      <li>Remote Automation</li>
    </ul>
    <p class="web">www.kvr.com</p>
  </div>
  <div class="rule rule--bottom"></div>
</section>

</body>
</html>
```